Quill Harbor (IT/Network Services)

Quill Harbor, LLC provides technology services to small and medium businesses. Essentially, anytime you've every thought your business might need an "IT guy" to handle something you could instead call us to handle it. Basically, you can outsource your IT needs to us.

This is a brand new company and so we'll need a brand new website. I'd like to use WordPress to handle the site since that will make things easier for me to maintain in the long run.

The site should include a, more-or-less, static front page with the dynamic data occurring on pages linked from a navigational area.

I have a logo already designed that I would like to see used in the design. The one with "white" in the title is the official logo, just added some other versions for your perusal.

Color queues from the logo but feel free to add other colors where applicable.

The site should feel somewhat corporate but with a "younger" slant (something a 25-35 year old would enjoy).

Pages (either to be added initially or by me after design completion):
"About" section - includes company history, business philosophy, etc.
"Services" section - service options, service approach, service specifics
"Testimonials" section - (eventually)
"News" section - (eventually) industry news, company news, events, blog
Contact Links

Websites to view:
The two largest local competitors:
http://www.brightmarsh-tech.example/
http://www.kelvarworks.example/
Other local competitors:
http://www.tpbllc.example/
http://www.morrowfield.example/

Other info you might find useful:
Domain: qhllc.example
Address:
417 Elm Row S
Suite 512B
Nashville, TN 37288
Phone: 615-555-0187
Emails available for use/display:
info@qhllc.example
sales@qhllc.example

Target Market(s)

Our target clients are mainly small businesses (25 or less computer users) which means we're looking at a lot of start-ups or younger companies. We'll be interacting with many entrepreneurs and young business owners.

Requirements
Must have
• Need full WP theme (not a mockup)

```html
<!DOCTYPE html>
<html lang="en">
<head>
<meta charset="utf-8">
<title>Quill Harbor — IT &amp; Network Services</title>
<link rel="stylesheet" href="https://fonts.googleapis.com/css2?family=PT+Sans+Narrow:wght@400;700&family=Marcellus&family=Arimo:wght@400;700&display=swap">
<style>
:root{
  --orange:#f09a00;
  --orange-dark:#d98400;
  --ink:#2e2e2e;
  --body:#3c3c3c;
  --grey-logo:#6f6f6f;
  --band:#f4f3f1;
  --rule:#c9c9c9;
  --footer:#3f3f3f;
  --footer-text:#cfcfcf;
  --white:#fff;
}
*{margin:0;padding:0;box-sizing:border-box}
html,body{width:1200px;height:1171px;overflow:hidden}
body{position:relative;background:var(--white);font-family:"Arimo",Arial,sans-serif;color:var(--body)}
.abs{position:absolute}
.narrow{font-family:"PT Sans Narrow",sans-serif}

/* header */
.brand{left:88px;top:28px;display:flex;align-items:center;gap:14px;font-family:"PT Sans Narrow",sans-serif;font-weight:700;font-size:58px;color:var(--grey-logo);letter-spacing:1px;line-height:60px}
.brand-dot{width:34px;height:34px;border-radius:50%;background:var(--orange)}
.search{left:861px;top:10px;width:220px;height:28px;background:#f1efec;border:1px solid #e6e3df}
.search svg{position:absolute;right:8px;top:6px}
.nav{top:42px;font-family:"PT Sans Narrow",sans-serif;font-size:19px;color:var(--ink)}
.nav .num{font-size:13px;margin-right:3px}
.nav .sub{display:block;font-family:"Arimo",Arial,sans-serif;font-style:italic;font-size:13px;margin-top:13px;color:#222}
.nav-item{position:absolute;white-space:nowrap}
.nav-item .label{display:inline-block;padding:5px 8px;border-radius:6px}
.nav-item.active .label{background:var(--orange);color:var(--white)}

/* hero */
.hero{left:0;top:104px;width:1200px;height:397px;background:linear-gradient(180deg,var(--orange-dark),var(--orange))}
.frame{left:88px;top:127px;width:538px;height:350px;background:var(--white);box-shadow:0 1px 4px rgba(0,0,0,.25)}
.photo{left:98px;top:136px;width:518px;height:333px;background:linear-gradient(160deg,#e9edf2 0%,#c4ccd8 45%,#2a3450 75%,#1b2236 100%)}
.hero-title{left:673px;top:153px;font-family:"Marcellus",serif;color:var(--white);font-size:30px;line-height:36px}
.hero-title .big{font-size:38px}
.hero-copy{left:677px;top:241px;width:435px;color:var(--white);font-size:13.5px;line-height:24px;text-align:justify}
.btn{display:flex;align-items:center;justify-content:center;gap:10px;background:linear-gradient(#fff,#e2e2e2);border:1px solid #d6d6d6;font-family:"Arimo",Arial,sans-serif;font-weight:700;font-style:italic;color:#a9a9a9;font-size:17px}
.btn .chev{width:16px;height:16px;border-radius:50%;background:#ededed;display:flex;align-items:center;justify-content:center}
.dots{left:677px;top:422px;display:flex;gap:8px}
.dots span{width:16px;height:16px;border-radius:50%;background:var(--white)}
.dots span.on{background:#111}

/* features */
.features{left:0;top:501px;width:1200px;height:212px;background:var(--band)}
.feature{position:absolute;top:522px}
.feature .icon{position:absolute;left:0;top:0;width:60px;height:60px;border-radius:50%;border:5px solid #3a3a3a;background:var(--white);display:flex;align-items:center;justify-content:center}
.feature h2{position:absolute;left:72px;top:12px;font-family:"PT Sans Narrow",sans-serif;font-weight:400;font-size:30px;color:#222;white-space:nowrap}
.feature p{position:absolute;left:2px;top:68px;width:315px;font-size:13.5px;line-height:24px;text-align:justify}
.go{display:inline-flex;width:18px;height:18px;border-radius:50%;background:#e6e4e1;align-items:center;justify-content:center;vertical-align:middle;margin-left:10px}

/* panels */
.panel{top:733px;height:326px;border:1px solid var(--rule);border-top:14px solid var(--orange);background:var(--white)}
.panel h3{position:absolute;left:25px;top:18px;font-family:"PT Sans Narrow",sans-serif;font-weight:400;font-size:30px;color:#222}
.date{position:absolute;left:23px;color:var(--orange);font-weight:700;font-size:18px}
.panel p{position:absolute;font-size:13.5px;line-height:24px;text-align:justify}
.author{position:absolute;right:30px;color:var(--orange);font-weight:700;font-size:18px}

/* footer */
.footer{left:0;top:1079px;width:1200px;height:92px;background:var(--footer)}
.footer-nav{left:88px;top:1104px;font-family:"PT Sans Narrow",sans-serif;font-size:14px;color:var(--footer-text)}
.footer-nav span{margin:0 5px}
.copyright{left:88px;top:1132px;font-family:"PT Sans Narrow",sans-serif;font-size:14px;color:var(--footer-text)}
.social{top:1102px;width:46px;height:46px;border-radius:4px}
</style>
</head>
<body>

<header>
  <div class="abs brand"><span>Quill Harbor</span><span class="brand-dot"></span></div>
  <div class="abs search">
    <svg width="16" height="16" viewBox="0 0 16 16"><circle cx="9" cy="6.5" r="4.5" fill="none" stroke="#555" stroke-width="1.6"/><line x1="5.8" y1="9.8" x2="2" y2="13.6" stroke="#555" stroke-width="2"/></svg>
  </div>
  <nav class="abs nav" style="left:0;width:1200px">
    <div class="nav-item active" style="left:513px"><span class="label"><span class="num">01</span>HOME</span><span class="sub" style="margin-top:6px;margin-left:4px">Welcome page</span></div>
    <div class="nav-item" style="left:632px"><span class="label"><span class="num">02</span>ABOUT</span><span class="sub" style="margin-top:6px;margin-left:9px">Who We Are</span></div>
    <div class="nav-item" style="left:734px"><span class="label"><span class="num">03</span>SOLUTIONS</span><span class="sub" style="margin-top:6px;margin-left:8px">What We Do</span></div>
    <div class="nav-item" style="left:865px"><span class="label"><span class="num">04</span>SERVICES</span><span class="sub" style="margin-top:6px;margin-left:8px">What We Offer</span></div>
    <div class="nav-item" style="left:986px"><span class="label"><span class="num">05</span>CONTACT US</span><span class="sub" style="margin-top:6px;margin-left:9px">Stay in Touch</span></div>
  </nav>
</header>

<section>
  <div class="abs hero"></div>
  <div class="abs frame"></div>
  <div class="abs photo" role="img" aria-label="Photo of business people shaking hands in an office"></div>
  <h1 class="abs hero-title" style="font-weight:400">Build <span class="big">Your Business</span><br>With Us!</h1>
  <p class="abs hero-copy">Lorem ipsum dolor sit amet, consectetur adipisicing elit, sed do eiusmod tempor incididunt ut labore et dolore magna aliqua. Ut enim ad minim veniam, quis nostrud exercitation ullamco laboris nisi ut aliquip ex ea commodo consequat.</p>
  <a class="abs btn" style="left:677px;top:356px;width:99px;height:40px">More <span class="chev"><svg width="6" height="8" viewBox="0 0 6 8"><path d="M1 1l3 3-3 3" fill="none" stroke="#999" stroke-width="1.5"/></svg></span></a>
  <div class="abs dots"><span class="on"></span><span></span><span></span><span></span><span></span></div>
</section>

<section>
  <div class="abs features"></div>
  <div class="feature" style="left:87px">
    <div class="icon"><svg width="26" height="26" viewBox="0 0 26 26"><circle cx="13" cy="11" r="8" fill="#444"/><path d="M13 19v4M8 24h10" stroke="#444" stroke-width="2"/></svg></div>
    <h2>Effective Solutions</h2>
    <p>Lorem ipsum dolor sit amet, consectetur adipisicing elit, sed do eiusmod tempor incididunt ut labore et dolore magna aliqua. Ut enim ad minim veniam, quis nostrud exercitation.<span class="go"><svg width="6" height="8" viewBox="0 0 6 8"><path d="M1 1l3 3-3 3" fill="none" stroke="#999" stroke-width="1.5"/></svg></span></p>
  </div>
  <div class="feature" style="left:433px">
    <div class="icon"><svg width="28" height="28" viewBox="0 0 28 28"><circle cx="14" cy="14" r="12" fill="#444"/><path d="M2 14h24M14 2c-5 6-5 18 0 24M14 2c5 6 5 18 0 24" fill="none" stroke="#fff" stroke-width="1.2"/></svg></div>
    <h2 style="left:78px">Success Strategies</h2>
    <p style="left:5px">Lorem ipsum dolor sit amet, consectetur adipisicing elit, sed do eiusmod tempor incididunt ut labore et dolore magna aliqua. Ut enim ad minim veniam, quis nostrud exercitation.<span class="go"><svg width="6" height="8" viewBox="0 0 6 8"><path d="M1 1l3 3-3 3" fill="none" stroke="#999" stroke-width="1.5"/></svg></span></p>
  </div>
  <div class="feature" style="left:790px">
    <div class="icon"><svg width="30" height="26" viewBox="0 0 30 26"><circle cx="11" cy="8" r="5" fill="#444"/><path d="M2 22c0-6 4-9 9-9s9 3 9 9z" fill="#444"/><circle cx="20" cy="7" r="4" fill="#444"/><path d="M18 12c5 0 9 3 9 9h-5" fill="#444"/></svg></div>
    <h2 style="left:79px">24/7 Support</h2>
    <p style="left:4px">Lorem ipsum dolor sit amet, consectetur adipisicing elit, sed do eiusmod tempor incididunt ut labore et dolore magna aliqua. Ut enim ad minim veniam, quis nostrud exercitation.<span class="go"><svg width="6" height="8" viewBox="0 0 6 8"><path d="M1 1l3 3-3 3" fill="none" stroke="#999" stroke-width="1.5"/></svg></span></p>
  </div>
</section>

<section>
  <div class="abs panel" style="left:88px;width:497px">
    <h3>Latest News</h3>
    <div class="date" style="top:63px">12-05-2012</div>
    <p style="left:25px;top:91px;width:448px">Lorem ipsum dolor sit amet, consectetur adipisicing elit, sed do eiusmod tempor incididunt ut labore et dolore magna aliqua. Ut enim ad minim veniam, quis nostrud exercitation.</p>
    <div class="date" style="top:173px">12-05-2012</div>
    <p style="left:25px;top:200px;width:448px">Lorem ipsum dolor sit amet, consectetur adipisicing elit, sed do eiusmod tempor incididunt ut labore et dolore magna aliqua.</p>
    <a class="abs btn" style="left:371px;top:256px;width:101px;height:41px">More <span class="chev"><svg width="6" height="8" viewBox="0 0 6 8"><path d="M1 1l3 3-3 3" fill="none" stroke="#999" stroke-width="1.5"/></svg></span></a>
  </div>
  <div class="abs panel" style="left:621px;width:491px">
    <h3 style="left:27px">Testimonials</h3>
    <p style="left:29px;top:62px;width:432px">“Lorem ipsum dolor sit amet, consectetur adipisicing elit, sed do eiusmod tempor incididunt ut labore et dolore magna aliqua. Ut enim ad minim veniam, quis nostrud exercitation.”</p>
    <div class="author" style="top:128px">- Lorem Ipsum</div>
    <p style="left:29px;top:169px;width:432px">“Lorem ipsum dolor sit amet, consectetur adipisicing elit, sed do eiusmod tempor incididunt ut labore et dolore magna aliqua.</p>
    <div class="author" style="top:219px">- Lorem Ipsum</div>
    <a class="abs btn" style="left:359px;top:256px;width:101px;height:41px">More <span class="chev"><svg width="6" height="8" viewBox="0 0 6 8"><path d="M1 1l3 3-3 3" fill="none" stroke="#999" stroke-width="1.5"/></svg></span></a>
  </div>
</section>

<footer>
  <div class="abs footer"></div>
  <div class="abs footer-nav">HOME<span>|</span>ABOUT<span>|</span>SOLUTIONS<span>|</span>SERVICES<span>|</span>CONTACT US</div>
  <div class="abs copyright">© 2012. ALL RIGHTS RESERVED.</div>
  <div class="abs social" style="left:1004px;background:#3b5a94" role="img" aria-label="Social profile link"></div>
  <div class="abs social" style="left:1065px;background:#3fa9d8" role="img" aria-label="Social profile link"></div>
</footer>

</body>
</html>
```